All-Natural Head Lice Removal company

I need a business card with my pre-existing logo. We are a new company located in Portland Oregon that goes into peoples homes to help with head lice removal. My products and approach are all- natural and also will be around children.On my current logo we used Teal Bl and the color Green. I am open to new ideas just want it simple and creative

Target Market(s)

my biggest market is families of school aged children

Industry/Entity Type

Business

Contact Information for Business Card

see upload for details from previous business card

Font styles to use
Serif

Colors
33a6d7
9bcb3b
f37122

Requirements
Must have
• Basic information/ logo put into a creative format that is catching to the eye
Nice to have
• creative

```html
<!DOCTYPE html>
<html lang="en">
<head>
<meta charset="utf-8">
<title>Clear Nits – Business Card, Back and Front</title>
<link href="https://fonts.googleapis.com/css2?family=Comic+Neue:wght@400;700&display=swap" rel="stylesheet">
<style>
  :root {
    --page-bg: #e9e7e3;
    --card-white: #ffffff;
    --brand-blue: #1e8fcf;
    --brand-blue-deep: #1676b3;
    --brand-green: #7dc242;
    --stripe-dark: #222326;
    --logo-ink: #2b2b2d;
    --text-light: #ffffff;
    --social-tile: #3b5b98;
  }
  html, body {
    margin: 0;
    width: 1200px;
    height: 843px;
    overflow: hidden;
    background: var(--page-bg);
  }
  .business-card {
    position: absolute;
    top: 261px;
    width: 560px;
    height: 320px;
    border-radius: 18px;
    overflow: hidden;
    box-shadow: 0 8px 24px rgba(0,0,0,0.18);
    font-family: "Comic Neue", "Comic Sans MS", cursive;
  }
  .card-back {
    left: 25px;
    background: linear-gradient(180deg, var(--brand-blue), var(--brand-blue-deep));
  }
  .card-front {
    left: 615px;
    background: var(--card-white);
  }
  .card-wave {
    position: absolute;
    inset: 0;
    width: 100%;
    height: 100%;
  }
  .brand-logo {
    position: absolute;
    display: flex;
    align-items: center;
    gap: 12px;
  }
  .brand-mark {
    width: 62px;
    height: 62px;
    border-radius: 50%;
    background: var(--brand-green);
  }
  .brand-name {
    font-size: 34px;
    font-weight: 700;
    color: var(--logo-ink);
  }
  .card-back .brand-logo {
    left: 50%;
    top: 70px;
    transform: translateX(-50%);
  }
  .card-front .brand-logo {
    left: 62px;
    top: 58px;
  }
  .back-tagline {
    position: absolute;
    left: 0;
    right: 0;
    top: 178px;
    margin: 0;
    text-align: center;
    color: var(--text-light);
    font-size: 17px;
    line-height: 1.3;
  }
  .social-tile {
    position: absolute;
    right: 30px;
    top: 140px;
    width: 32px;
    height: 32px;
    border-radius: 5px;
    background: var(--social-tile);
  }
  .contact-block {
    position: absolute;
    right: 32px;
    top: 184px;
    text-align: right;
    color: var(--text-light);
  }
  .contact-name {
    font-size: 20px;
    font-weight: 700;
    margin: 0;
    letter-spacing: 0.5px;
  }
  .contact-role {
    font-size: 15px;
    margin: 1px 0 12px;
  }
  .contact-line {
    font-size: 15px;
    margin: 0 0 3px;
  }
</style>
</head>
<body>
  <div class="business-card card-back">
    <div class="brand-logo">
      <div class="brand-mark"></div>
      <div class="brand-name">Clear Nits</div>
    </div>
    <p class="back-tagline">Try Clear Nits Today, Be Lice Free Tomorrow!<br>All Natural Lice Removal Services</p>
  </div>

  <div class="business-card card-front">
    <svg class="card-wave" viewBox="0 0 1000 571" preserveAspectRatio="none" aria-hidden="true">
      <defs>
        <linearGradient id="blueFill" x1="0" y1="0" x2="0" y2="1">
          <stop offset="0" stop-color="#1e8fcf"/>
          <stop offset="1" stop-color="#1676b3"/>
        </linearGradient>
      </defs>
      <path d="M0,314 C220,420 360,400 560,300 S860,160 1000,150 L1000,571 L0,571 Z" fill="#222326"/>
      <path d="M0,320 C220,428 360,410 560,312 S860,176 1000,170 L1000,571 L0,571 Z" fill="#ffffff"/>
      <path d="M0,324 C220,434 360,418 560,322 S860,186 1000,182 L1000,571 L0,571 Z" fill="#7dc242"/>
      <path d="M0,334 C220,446 360,432 560,338 S860,204 1000,200 L1000,571 L0,571 Z" fill="url(#blueFill)"/>
    </svg>

    <div class="brand-logo">
      <div class="brand-mark"></div>
      <div class="brand-name">Clear Nits</div>
    </div>

    <div class="social-tile"></div>

    <div class="contact-block">
      <p class="contact-name">Mara Colton</p>
      <p class="contact-role">Owner</p>
      <p class="contact-line">1-855-555-NITS (6487)</p>
      <p class="contact-line">mara@clearnits.com</p>
      <p class="contact-line">www.clearnits.com</p>
    </div>
  </div>
</body>
</html>
```